Flyers

Modify Existing Flyer and create another for exterior company
Updates

Previous Brief has been updated- we want to update this existing one also

Target Market(s)

Exterior Remodeling Customers

Industry/Entity Type

Remodeling/Construction

```html
<!DOCTYPE html>
<html lang="en">
<head>
<meta charset="utf-8">
<title>Harlow Roofing &amp; Exteriors – Flyer</title>
<link href="https://fonts.googleapis.com/css2?family=Poppins:wght@400;500;600;700&family=Montserrat:wght@400;500;600&display=swap" rel="stylesheet">
<style>
  :root{
    --navy:#121a2e;
    --blue:#1a6ad0;
    --orange:#f05a22;
    --ink:#1b1d24;
    --paper:#f7f7f8;
    --stage:#e8e8e8;
    --white:#ffffff;
  }
  *{box-sizing:border-box;margin:0;padding:0}
  html,body{width:1200px;height:2294px;overflow:hidden;background:var(--stage)}
  .canvas{position:relative;width:1200px;height:2294px;overflow:hidden}
  .flyer{position:absolute;left:0;top:371px;width:1052px;height:1360px;transform:scale(1.14068);transform-origin:0 0;background:var(--paper);overflow:hidden;font-family:"Montserrat",sans-serif;color:var(--ink)}
  .abs{position:absolute}
  .header-art{position:absolute;left:0;top:0}
  .photo{position:absolute}
  .brand{left:62px;top:112px;width:300px;font-family:"Poppins",sans-serif;font-weight:600;font-size:24px;line-height:1.15;color:var(--white);letter-spacing:.5px;display:flex;align-items:center;gap:12px}
  .brand-mark{width:18px;height:18px;background:var(--orange);flex:none}
  .headline{left:62px;top:220px;font-family:"Poppins",sans-serif;color:var(--white);font-size:31px;line-height:32px;text-transform:uppercase;font-weight:400}
  .headline strong{display:block;color:var(--navy);font-weight:700;font-size:33px;line-height:36px}
  .accent-bar{left:62px;top:331px;width:70px;height:6px;background:var(--navy)}
  .tagline{left:62px;top:352px;font-family:"Poppins",sans-serif;font-weight:600;font-size:30px;line-height:38px;color:var(--ink)}
  .tagline span{display:block;color:var(--orange)}
  .section-title{font-family:"Poppins",sans-serif;font-weight:700;font-size:18px;color:var(--navy);text-transform:uppercase;white-space:nowrap}
  .section-title span{color:var(--blue)}
  .section-text{font-size:15px;line-height:18.5px;color:#2a2c33;white-space:nowrap}
  .frame-line{background:var(--orange)}
  .list{list-style:none;font-size:15px;line-height:15px;color:#2a2c33}
  .list li{position:absolute;padding-left:26px;white-space:nowrap}
  .list li::before{content:"";position:absolute;left:0;top:1px;width:11px;height:11px;border:1.5px solid var(--blue)}
  .list li::after{content:"";position:absolute;left:4px;top:0;width:4px;height:9px;border-right:2px solid var(--blue);border-bottom:2px solid var(--blue);transform:rotate(40deg)}
  .cta-band{left:0;top:1155px;width:470px;height:92px;background:var(--navy)}
  .cta-small{left:62px;top:1164px;font-family:"Poppins",sans-serif;font-size:22px;color:var(--white);text-transform:uppercase}
  .cta-big{left:62px;top:1188px;font-family:"Poppins",sans-serif;font-weight:700;font-size:39px;color:var(--orange);text-transform:uppercase}
  .phone{left:62px;top:1247px;display:flex;align-items:center;gap:10px;font-family:"Poppins",sans-serif;font-weight:700;font-size:43px;color:var(--white);letter-spacing:1px}
  .web-strip{left:560px;top:1260px;width:492px;height:38px;background:var(--orange)}
  .web{left:610px;top:1264px;width:420px;text-align:center;white-space:nowrap;font-family:"Poppins",sans-serif;font-weight:500;font-size:22px;letter-spacing:8px;color:var(--white)}
  .hex{clip-path:polygon(25% 0,75% 0,100% 50%,75% 100%,25% 100%,0 50%)}
</style>
</head>
<body>
<div class="canvas">
  <div class="flyer">

    <svg class="header-art" width="1052" height="360" viewBox="0 0 1052 360" aria-hidden="true">
      <defs>
        <linearGradient id="roofTone" x1="0" y1="0" x2="1" y2="1">
          <stop offset="0" stop-color="#2b2f36"/>
          <stop offset=".55" stop-color="#4a4d52"/>
          <stop offset="1" stop-color="#9a7a5a"/>
        </linearGradient>
      </defs>
      <polygon points="350,0 1052,0 1052,340 598,340" fill="url(#roofTone)"/>
      <polygon points="0,0 350,0 500,205 0,205" fill="var(--navy)"/>
      <polygon points="0,205 500,205 595,335 0,335" fill="var(--orange)"/>
      <polyline points="350,0 600,342 1052,342" fill="none" stroke="var(--blue)" stroke-width="10"/>
      <rect x="0" y="0" width="350" height="6" fill="var(--blue)"/>
    </svg>
    <div class="photo" role="img" aria-label="Roofers installing a dark metal roof on a timber house" style="left:350px;top:0;width:0;height:0"></div>

    <div class="abs hex" style="left:702px;top:218px;width:236px;height:206px;background:var(--blue)"></div>
    <div class="abs hex" role="img" aria-label="Painter on scaffolding repainting a red exterior wall" style="left:714px;top:228px;width:212px;height:186px;background:linear-gradient(160deg,#cfd6df 0%,#b9c1cb 45%,#c0303a 75%,#9c2630 100%)"></div>

    <div class="abs brand"><span class="brand-mark"></span>Harlow Roofing &amp; Exteriors</div>

    <div class="abs headline">Ready for a<br>Beautiful &amp; Functional<strong>Roofing and Exterior ?</strong></div>
    <div class="abs accent-bar"></div>

    <div class="abs tagline">Work With Top-Rated Local<span>Remodeling Company In Ankeny, LA</span></div>

    <!-- Roofing services -->
    <div class="abs section-title" style="left:62px;top:480px">Roofing <span>Services</span></div>
    <div class="abs frame-line" style="left:62px;top:509px;width:252px;height:2px"></div>
    <div class="abs frame-line" style="left:312px;top:509px;width:2px;height:81px"></div>
    <div class="abs frame-line" style="left:312px;top:588px;width:215px;height:2px"></div>
    <div class="photo" role="img" aria-label="Roofer in hi-vis vest working on a shingle roof" style="left:325px;top:458px;width:202px;height:120px;background:linear-gradient(135deg,#6f7b86,#a9b7c2 45%,#c9c23a 70%,#56503f)"></div>
    <p class="abs section-text" style="left:62px;top:518px">Whatever your vision is for<br>your new roofing, our crew<br>can help you bring it to life.<br>You can trust us for:</p>
    <ul class="list">
      <li style="left:62px;top:607px">Roofing system<br>installation.</li>
      <li style="left:62px;top:653px">Roofing repairs.</li>
      <li style="left:62px;top:684px">Leak diagnosis repairs.</li>
      <li style="left:62px;top:715px">Ventillation repairs.</li>
      <li style="left:62px;top:746px">Skylights.</li>
      <li style="left:62px;top:777px">Repair chimney<br>flashing.</li>
      <li style="left:283px;top:607px">Shingles or even<br>sheets.</li>
      <li style="left:283px;top:653px">24 hour repair service.</li>
    </ul>

    <!-- Exterior services -->
    <div class="abs section-title" style="left:62px;top:861px">Exterior <span>Services</span></div>
    <div class="abs frame-line" style="left:62px;top:889px;width:252px;height:2px"></div>
    <div class="abs frame-line" style="left:312px;top:889px;width:2px;height:80px"></div>
    <div class="abs frame-line" style="left:312px;top:967px;width:215px;height:2px"></div>
    <div class="photo" role="img" aria-label="House with dormer windows and a worker on a ladder washing siding" style="left:325px;top:835px;width:202px;height:120px;background:linear-gradient(180deg,#5a4d45 0%,#6b5c52 45%,#c9bfae 60%,#b7ab98 100%)"></div>
    <p class="abs section-text" style="left:62px;top:898px">When you hire us for your<br>exterior project, the possibilities<br>are endless. Our experienced<br>and talented team can:</p>
    <ul class="list">
      <li style="left:62px;top:993px">Wall washing and<br>painting.</li>
      <li style="left:62px;top:1039px">Fence Installation &amp;<br>Repair.</li>
      <li style="left:62px;top:1085px">Holiday Lighting &amp;<br>Decorations</li>
      <li style="left:270px;top:993px">Gutter Cleaning &amp; Gutter<br>Repair.</li>
      <li style="left:270px;top:1039px">Soffit, Fascia &amp; Siding<br>Repair.</li>
    </ul>

    <!-- Home additions -->
    <div class="abs section-title" style="left:555px;top:480px">Home <span>Additions</span></div>
    <div class="abs frame-line" style="left:555px;top:508px;width:222px;height:2px"></div>
    <div class="abs frame-line" style="left:775px;top:508px;width:2px;height:78px"></div>
    <div class="abs frame-line" style="left:775px;top:584px;width:215px;height:2px"></div>
    <div class="photo" role="img" aria-label="Bright living room with grey sofa and potted plant" style="left:788px;top:453px;width:202px;height:120px;background:linear-gradient(90deg,#e9ebe8 0%,#d8d6d0 45%,#b5b2ab 100%)"></div>
    <p class="abs section-text" style="left:555px;top:517px">No matter what kind of<br>space you need our team<br>will bring your vision to life.<br>You can hire us if you<br>need a:</p>
    <ul class="list">
      <li style="left:557px;top:628px">Bathroom addition.</li>
      <li style="left:557px;top:659px">Bedroom addition.</li>
      <li style="left:557px;top:690px">Garage addition.</li>
      <li style="left:557px;top:721px">Basement addition.</li>
      <li style="left:763px;top:628px">Guest room addition.</li>
      <li style="left:763px;top:659px">Living room addition.</li>
      <li style="left:763px;top:690px">Sunroom addition.</li>
    </ul>

    <!-- Decks / patios -->
    <div class="abs section-title" style="left:549px;top:785px">Decks <span style="color:var(--navy)">/</span> <span>Patios</span></div>
    <div class="abs frame-line" style="left:549px;top:813px;width:228px;height:2px"></div>
    <div class="abs frame-line" style="left:775px;top:813px;width:2px;height:78px"></div>
    <div class="abs frame-line" style="left:775px;top:889px;width:215px;height:2px"></div>
    <div class="photo" role="img" aria-label="Patio with blue and green wicker chairs" style="left:788px;top:758px;width:202px;height:120px;background:linear-gradient(90deg,#e4d5bd 0%,#cfc0a8 40%,#8fa5b4 70%,#5f9a4a 100%)"></div>
    <p class="abs section-text" style="left:549px;top:822px">An outdoor space is a great<br>addition to any residential<br>property. When you decide<br>to build a patio or deck,<br>you'll be able to experience<br>a variety of benefits. Your<br>outdoor area will increase your:</p>
    <ul class="list">
      <li style="left:549px;top:977px">Property value.</li>
      <li style="left:549px;top:1008px">Curb appeal.</li>
      <li style="left:760px;top:975px">Functional living space.</li>
    </ul>

    <!-- footer -->
    <div class="abs" style="left:0;top:1190px;width:1052px;height:170px;background:var(--blue)"></div>
    <div class="abs cta-band"></div>
    <div class="abs web-strip"></div>

    <div class="abs hex" style="left:408px;top:1149px;width:190px;height:166px;background:var(--navy)"></div>
    <div class="abs hex" role="img" aria-label="Red tiled roof under a blue sky" style="left:417px;top:1157px;width:172px;height:150px;background:linear-gradient(180deg,#2f7fd6 0%,#69a9e6 40%,#d82c2c 60%,#b5201f 100%)"></div>
    <div class="abs hex" style="left:578px;top:1063px;width:216px;height:188px;background:var(--navy)"></div>
    <div class="abs hex" role="img" aria-label="Sunset view over hills from a deck railing" style="left:588px;top:1072px;width:196px;height:170px;background:linear-gradient(180deg,#d7d4c6 0%,#e8c88a 35%,#8a8f6a 65%,#4c5240 100%)"></div>
    <div class="abs hex" style="left:778px;top:1063px;width:216px;height:188px;background:var(--navy)"></div>
    <div class="abs hex" role="img" aria-label="Brick house with blue roof and lit windows at dusk" style="left:788px;top:1072px;width:196px;height:170px;background:linear-gradient(180deg,#1e3a6a 0%,#2c4f86 40%,#8a4a34 60%,#3e3a2c 100%)"></div>

    <div class="abs cta-small">Call today for your</div>
    <div class="abs cta-big">Free Estimate</div>
    <div class="abs phone">
      <svg width="30" height="30" viewBox="0 0 30 30" aria-hidden="true">
        <rect x="1.5" y="1.5" width="27" height="27" rx="7" fill="none" stroke="var(--orange)" stroke-width="2.5"/>
        <path d="M10 8c1-1 2-.5 2.5.5l1 2c.4.8 0 1.5-.6 2l-.8.6c.8 1.8 2.2 3.2 4 4l.6-.8c.5-.6 1.2-1 2-.6l2 1c1 .5 1.5 1.5.5 2.5-1.5 1.5-3.5 1.8-6 .3-2.7-1.6-4.9-3.8-6.4-6.4C7.4 11.5 8.5 9.5 10 8z" fill="var(--orange)"/>
      </svg>
      555-014-2287
    </div>
    <div class="abs web">www.harlowroof.com</div>

  </div>
</div>
</body>
</html>
```